Harborline marketing postcards (6x9)

I would like to replicate this 6x9 postcard, but update name/logo, phone number, web address, etc. I also need to create a second postcard copying this basic design, but with updated content and background pictures. Updated contact info to be used for both postcards:
Website: www.harborlinerealty.com
Name: Mark Fenwick
Email: mfenwick@harborlinerealty.com
Phone: (555) 246-8013

Requirements
Must have
• Need two 6x9 postcard designs; 1 themed for KV-Lorrin, 1 for Delvar R&K. Have uploaded photos that can be used in design. KV can be used for KV postcard (only), R&K can be used for R&K (only), Generic can be used for either. I've tried to upload extra photos so that you can use your creativity in selecting those that work best in the design.
Nice to have
• In the "Color palette" file, it has the two color schemes -- one for KV-Lorrin and one for Delvar R&K. Those respective color schemes should be heavily represented in each design. Then there are different groups of pictures labelled either "R&K" or "KV", plus some labelled "Generic". The generic ones can be used in either design, the others should be used only for the design for that school.

```html
<!DOCTYPE html>
<html lang="en">
<head>
<meta charset="utf-8">
<title>Harborline Residential – Postcards</title>
<link rel="stylesheet" href="https://fonts.googleapis.com/css2?family=Montserrat:wght@500;600;700;800&display=swap">
<style>
  :root {
    --brand: #4c55b8;
    --brand-band: rgba(76, 85, 184, 0.92);
    --ink: #1f2230;
    --white: #ffffff;
    --page: #f4f4f6;
    --rule-grey: #7a7a7a;
  }
  * { box-sizing: border-box; margin: 0; padding: 0; }
  html, body { width: 1200px; height: 2400px; overflow: hidden; }
  body {
    background: var(--page);
    font-family: "Montserrat", Arial, sans-serif;
    color: var(--white);
    position: relative;
  }

  /* Each card is built at 1040 x 693 and scaled to fit both sets on the canvas */
  .postcard {
    position: absolute;
    left: 184px;
    width: 1040px;
    height: 693px;
    overflow: hidden;
    transform: scale(0.8);
    transform-origin: top left;
    box-shadow: 0 10px 40px rgba(0, 0, 0, 0.18);
  }
  .postcard--kv-front { top: 36px; }
  .postcard--kv-back { top: 614px; }
  .postcard--rk-front { top: 1232px; }
  .postcard--rk-back { top: 1810px; }
  .postcard--back { background: var(--white); }

  /* Front */
  .front-photo { position: absolute; inset: 0; }
  .front-photo--kv {
    background: linear-gradient(180deg, #94b3dc 0%, #c9d8ec 28%, #d8c9b0 46%, #46702c 62%, #5f9034 82%, #3a6022 100%);
  }
  .front-photo--rk {
    background: linear-gradient(180deg, #a2bde0 0%, #cbd8ea 30%, #d9cbb6 48%, #3f6a2a 62%, #5e8f32 82%, #3d6424 100%);
  }
  .front-shade {
    position: absolute; inset: 0;
    background: linear-gradient(90deg, rgba(20, 40, 10, 0.45) 0%, rgba(20, 40, 10, 0) 55%);
  }
  .brand-band {
    position: absolute; left: 0; right: 0; top: 61px; height: 98px;
    background: var(--brand-band);
    display: flex; align-items: center;
    padding-left: 64px;
  }
  .brand-name {
    font-weight: 700; font-size: 34px; letter-spacing: 0.5px;
    text-transform: uppercase; color: var(--white);
  }
  .front-copy { position: absolute; left: 67px; top: 478px; }
  .school-name { font-size: 24px; font-weight: 600; margin-bottom: 12px; }
  .headline { font-size: 33px; font-weight: 800; line-height: 1.2; }
  .cta-box {
    position: absolute; left: 520px; top: 504px; width: 449px; height: 132px;
    background: var(--brand-band); border-radius: 10px;
    padding: 22px 28px;
  }
  .cta-lead { font-size: 22px; font-weight: 700; line-height: 1.32; }
  .cta-note { font-size: 16px; font-weight: 500; margin-top: 10px; }
  .front-rule { position: absolute; left: 0; right: 0; bottom: 0; height: 9px; background: var(--brand); }

  /* Back */
  .tile { position: absolute; width: 279px; height: 282px; border-radius: 12px; }
  .tile--text {
    background: var(--brand);
    font-size: 15px; font-weight: 500; line-height: 1.42;
    padding: 48px 30px 30px 42px;
  }
  .tile--text p + p { margin-top: 20px; }
  .tile--intro { left: 29px; top: 22px; }
  .tile--student {
    left: 313px; top: 22px;
    background: linear-gradient(160deg, #8fa9cf 0%, #e8e9ef 45%, #5f7fb8 100%);
  }
  .tile--capitol {
    left: 29px; top: 310px;
    background: linear-gradient(180deg, #7fa6d8 0%, #cdbfa6 45%, #4f7a2c 75%, #3b5e22 100%);
  }
  .tile--contact { left: 313px; top: 310px; padding: 82px 14px 30px 32px; }
  .stamp-box {
    position: absolute; left: 895px; top: 33px; width: 100px; height: 99px;
    border: 1px solid var(--rule-grey);
  }
  .footer {
    position: absolute; left: 32px; top: 612px;
    display: flex; align-items: flex-start; color: var(--ink);
  }
  .company { font-size: 19px; font-weight: 500; line-height: 1.05; width: 120px; }
  .company::after {
    content: ""; display: block; width: 40px; height: 2px; background: var(--brand); margin-top: 10px;
  }
  .agent { color: var(--brand); font-weight: 600; margin-right: 14px; }
  .agent-name { font-size: 23px; letter-spacing: 0.3px; text-transform: uppercase; line-height: 1.05; }
  .agent-phone { font-size: 21px; display: flex; align-items: center; gap: 6px; line-height: 1.2; }
  .agent-phone svg { width: 16px; height: 16px; }
  .links {
    border-left: 2px solid var(--brand); padding-left: 12px;
    font-size: 16px; font-weight: 600; line-height: 1.55; height: 48px;
  }
</style>
</head>
<body>

<!-- KV-Lorrin set -->
<section class="postcard postcard--kv-front" aria-label="KV-Lorrin postcard front">
  <div class="front-photo front-photo--kv" role="img" aria-label="Photo of the KV-Lorrin campus tower and main building behind a green lawn framed by trees under a blue sky"></div>
  <div class="front-shade"></div>
  <header class="brand-band"><span class="brand-name">Harborline Residential</span></header>
  <div class="front-copy">
    <p class="school-name">KV-Lorrin</p>
    <h1 class="headline">Helping out-of-state<br>families save thousands<br>on Texas tuition costs.</h1>
  </div>
  <div class="cta-box">
    <p class="cta-lead">Our expert advice makes it<br>as easy as 1-2-3. Have questions?</p>
    <p class="cta-note">Email us to receive a copy of our FAQ.</p>
  </div>
  <div class="front-rule"></div>
</section>

<section class="postcard postcard--back postcard--kv-back" aria-label="KV-Lorrin postcard back">
  <div class="tile tile--text tile--intro">
    <p>KV-Lorrin parents, did you know you can save over $13,800 a semester in tuition?</p>
    <p>Establishing Texas residency through a property purchase is as easy as 1-2-3.</p>
  </div>
  <div class="tile tile--student" role="img" aria-label="Photo of a student in a denim jacket carrying books and a backpack"></div>
  <div class="tile tile--capitol" role="img" aria-label="Photo of a domed capitol building at the end of a tree-lined walkway"></div>
  <div class="tile tile--text tile--contact">
    <p>Contact us to learn how we have helped more than 500 families - and counting - save thousands on tuition.</p>
    <p>Let us help you too.</p>
  </div>
  <div class="stamp-box" aria-label="Postage area"></div>
  <footer class="footer">
    <div class="company">Harborline Realty</div>
    <div class="agent">
      <div class="agent-name">Mark Fenwick</div>
      <div class="agent-phone">
        <svg viewBox="0 0 24 24" aria-hidden="true"><path fill="currentColor" d="M6.6 10.8a15.1 15.1 0 0 0 6.6 6.6l2.2-2.2a1 1 0 0 1 1-.25 11.4 11.4 0 0 0 3.6.57 1 1 0 0 1 1 1V20a1 1 0 0 1-1 1A17 17 0 0 1 3 4a1 1 0 0 1 1-1h3.5a1 1 0 0 1 1 1c0 1.25.2 2.45.57 3.6a1 1 0 0 1-.25 1z"/></svg>
        (555) 246-8013
      </div>
    </div>
    <div class="links">
      <div>mfenwick@harborlinerealty.com</div>
      <div>www.harborlinerealty.com</div>
    </div>
  </footer>
</section>

<!-- Delvar R&K set -->
<section class="postcard postcard--rk-front" aria-label="Delvar R&amp;K postcard front">
  <div class="front-photo front-photo--rk" role="img" aria-label="Photo of the Delvar R&amp;K campus main building behind a green lawn framed by trees under a blue sky"></div>
  <div class="front-shade"></div>
  <header class="brand-band"><span class="brand-name">Harborline Residential</span></header>
  <div class="front-copy">
    <p class="school-name">Delvar R&amp;K</p>
    <h1 class="headline">Helping out-of-state<br>families save thousands<br>on Texas tuition costs.</h1>
  </div>
  <div class="cta-box">
    <p class="cta-lead">Our expert advice makes it<br>as easy as 1-2-3. Have questions?</p>
    <p class="cta-note">Email us to receive a copy of our FAQ.</p>
  </div>
  <div class="front-rule"></div>
</section>

<section class="postcard postcard--back postcard--rk-back" aria-label="Delvar R&amp;K postcard back">
  <div class="tile tile--text tile--intro">
    <p>Delvar R&amp;K parents, did you know you can save over $13,800 a semester in tuition?</p>
    <p>Establishing Texas residency through a property purchase is as easy as 1-2-3.</p>
  </div>
  <div class="tile tile--student" role="img" aria-label="Photo of a student in a denim jacket carrying books and a backpack"></div>
  <div class="tile tile--capitol" role="img" aria-label="Photo of a domed capitol building at the end of a tree-lined walkway"></div>
  <div class="tile tile--text tile--contact">
    <p>Contact us to learn how we have helped more than 500 families - and counting - save thousands on tuition.</p>
    <p>Let us help you too.</p>
  </div>
  <div class="stamp-box" aria-label="Postage area"></div>
  <footer class="footer">
    <div class="company">Harborline Realty</div>
    <div class="agent">
      <div class="agent-name">Mark Fenwick</div>
      <div class="agent-phone">
        <svg viewBox="0 0 24 24" aria-hidden="true"><path fill="currentColor" d="M6.6 10.8a15.1 15.1 0 0 0 6.6 6.6l2.2-2.2a1 1 0 0 1 1-.25 11.4 11.4 0 0 0 3.6.57 1 1 0 0 1 1 1V20a1 1 0 0 1-1 1A17 17 0 0 1 3 4a1 1 0 0 1 1-1h3.5a1 1 0 0 1 1 1c0 1.25.2 2.45.57 3.6a1 1 0 0 1-.25 1z"/></svg>
        (555) 246-8013
      </div>
    </div>
    <div class="links">
      <div>mfenwick@harborlinerealty.com</div>
      <div>www.harborlinerealty.com</div>
    </div>
  </footer>
</section>

</body>
</html>
```